Business Card Design Project

This is the first time we use our new logo. We need a business card that we can use both on our institutional corporate relationships and also that works for our staff that deals with consumers directly.

VELUNDA is a new company dedicated to empower consumers and to provide them with the best choices for specialized health care using the latest telemedicine technology (medicine at a distance via videoconference).

We want to print this cards in high quality materials and process. We will like designs that allow us to use UV spot varnish and other techniques that will differentiate us.

We are including Two different versions of Color logos. In addition we are including white over black background logos. Those can be used replacing the black for a color.

Please note this is the first time we will be creating any corporate materials with our new logo and colors.

Target Market(s)

34+ consumers of medium high and high socioeconomic levels.

Industry/Entity Type

Health

Requirements
Must have
• Our logo on its original colors
Should not have
• Any other graphical element or design that is not our logo

```html
<!DOCTYPE html>
<html lang="en">
<head>
<meta charset="utf-8">
<title>VELUNDA Business Card</title>
<link href="https://fonts.googleapis.com/css2?family=Montserrat:wght@500;700&family=Arimo:wght@400&display=swap" rel="stylesheet">
<style>
  :root {
    --page-bg: #e4e6e9;
    --card-black: #111214;
    --card-black-soft: #24262a;
    --brand-blue: #1d6195;
    --sky-blue: #4fb4e2;
    --band-blue: #1a5982;
    --teal: #2bb3a3;
    --white: #ffffff;
  }
  html, body {
    margin: 0;
    width: 1200px;
    height: 987px;
    overflow: hidden;
    background: var(--page-bg);
  }
  .canvas {
    position: relative;
    width: 1200px;
    height: 987px;
  }
  .card {
    position: absolute;
    left: 220px;
    width: 760px;
    height: 434px;
    border-radius: 26px;
    overflow: hidden;
    box-shadow: 0 8px 24px rgba(0,0,0,0.18);
  }
  .card--back { top: 48px; }
  .card--front { top: 508px; }
  .weave-fill {
    position: absolute;
    inset: 0;
    background: radial-gradient(ellipse at 50% 40%, var(--card-black-soft) 0%, var(--card-black) 75%);
  }
  .wordmark {
    position: absolute;
    display: flex;
    align-items: center;
    gap: 18px;
    font-family: "Montserrat", sans-serif;
    font-weight: 700;
    color: var(--brand-blue);
    letter-spacing: 2px;
  }
  .wordmark__dot {
    border-radius: 50%;
    background: var(--sky-blue);
  }
  .card--back .wordmark {
    left: 0; right: 0;
    top: 140px;
    justify-content: center;
    font-size: 72px;
  }
  .card--back .wordmark__dot { width: 30px; height: 30px; }
  .back-web {
    position: absolute;
    left: 0; right: 0;
    top: 250px;
    text-align: center;
    font-family: "Arimo", sans-serif;
    font-size: 26px;
    letter-spacing: 6px;
    color: var(--sky-blue);
  }
  .card--front .wordmark {
    left: 60px;
    top: 48px;
    font-size: 58px;
  }
  .card--front .wordmark__dot { width: 24px; height: 24px; }
  .holder {
    position: absolute;
    left: 60px;
    top: 140px;
    font-family: "Montserrat", sans-serif;
  }
  .holder__name {
    font-size: 30px;
    font-weight: 700;
    color: var(--sky-blue);
    margin: 0;
  }
  .holder__title {
    font-size: 18px;
    font-weight: 500;
    color: var(--teal);
    margin: 2px 0 0;
  }
  .band {
    position: absolute;
    inset: 0;
  }
  .contact {
    position: absolute;
    right: 48px;
    top: 270px;
    margin: 0;
    padding: 0;
    list-style: none;
    font-family: "Arimo", sans-serif;
    font-size: 21px;
    color: var(--white);
  }
  .contact li {
    display: flex;
    align-items: center;
    justify-content: flex-end;
    gap: 10px;
    line-height: 30px;
  }
  .contact svg { width: 18px; height: 18px; }
  .address {
    position: absolute;
    left: 48px;
    bottom: 26px;
    margin: 0;
    font-family: "Arimo", sans-serif;
    font-size: 20px;
    color: var(--white);
  }
</style>
</head>
<body>
<div class="canvas">

  <section class="card card--back">
    <div class="weave-fill" role="img" aria-label="Dark woven carbon-fibre texture background"></div>
    <div class="wordmark"><span class="wordmark__dot"></span>VELUNDA</div>
    <div class="back-web">www.velunda.com</div>
  </section>

  <section class="card card--front">
    <div class="weave-fill" role="img" aria-label="Dark woven carbon-fibre texture background"></div>
    <svg class="band" viewBox="0 0 760 434" preserveAspectRatio="none" aria-hidden="true">
      <path d="M0 170 C 60 250, 260 300, 760 236 L760 434 L0 434 Z" fill="var(--band-blue)"/>
      <path d="M0 150 C 50 235, 250 290, 560 268 C 300 282, 80 250, 0 190 Z" fill="var(--sky-blue)"/>
    </svg>
    <div class="wordmark"><span class="wordmark__dot"></span>VELUNDA</div>
    <div class="holder">
      <p class="holder__name">Your Name</p>
      <p class="holder__title">Title</p>
    </div>
    <ul class="contact">
      <li>
        <svg viewBox="0 0 20 20" aria-hidden="true"><circle cx="10" cy="10" r="9" fill="none" stroke="#fff" stroke-width="2"/><path d="M7 5 L9 8 L8 9 Q9 11 11 12 L12 11 L15 13 L13 15 Q8 15 5 7 Z" fill="#fff"/></svg>
        012-555-0147
      </li>
      <li>
        <svg viewBox="0 0 20 20" aria-hidden="true"><circle cx="10" cy="10" r="9" fill="none" stroke="#fff" stroke-width="2"/><path d="M7 5 L9 8 L8 9 Q9 11 11 12 L12 11 L15 13 L13 15 Q8 15 5 7 Z" fill="#fff"/></svg>
        012-555-0147
      </li>
      <li>
        <svg viewBox="0 0 20 20" aria-hidden="true"><rect x="2" y="5" width="16" height="11" fill="none" stroke="#fff" stroke-width="2"/><path d="M2 5 L10 11 L18 5" fill="none" stroke="#fff" stroke-width="2"/></svg>
        name@velunda.com
      </li>
      <li>
        <svg viewBox="0 0 20 20" aria-hidden="true"><circle cx="10" cy="10" r="8" fill="none" stroke="#fff" stroke-width="2"/><ellipse cx="10" cy="10" rx="3.5" ry="8" fill="none" stroke="#fff" stroke-width="1.5"/><path d="M2 10 H18" stroke="#fff" stroke-width="1.5"/></svg>
        www.velunda.com
      </li>
    </ul>
    <p class="address">Street Name, City Name, State, City Zip Code</p>
  </section>

</div>
</body>
</html>
```